New business card for a regional office of a US M&A company

We need business card for a finance company, office based in Hong Kong , our Head office is in US, our business is to Merge and acquires companies , the new office will be a regional office for the Asia Pacific region. We want to use the head office logo as attached ( but don't have to be exactly the same, can be a variation to it) as a base and then add Asia Pacific alongside the logo.
We would prefer to have be bilingual Eng + Chinese, although we don't really have Chinese company name .

Industry/Entity Type

Business

Contact Information for Business Card

Clara Jo Tsang
 

VP,
APAC M&A Operations
ORIN VANTAGE Asia Pacific Limited
 
Unit 1407, K18
18 Tai Lok Shan Road, 
Hong Kong 
 
M: +852 6038 1742
T : +852 2836 4100
F : +852 2836 4177
VOIP: 4158
 
cjtsang@orinvantage.com

Font styles to use
Serif
Sans Serif

Colors

Designer to choose colors to be used in the design.

Requirements
Must have
• APAC Office

```html
<!DOCTYPE html>
<html lang="en">
<head>
<meta charset="utf-8">
<title>Orin Vantage – APAC Business Card</title>
<link rel="stylesheet" href="https://fonts.googleapis.com/css2?family=Open+Sans:wght@700&family=Roboto:wght@400;500&family=Roboto+Condensed:wght@500&display=swap">
<style>
  :root {
    --stage: #2a2a2a;
    --navy: #0f2841;
    --cyan: #22b0d3;
    --white: #ffffff;
    --text-light: #e4e9ee;
  }
  * { margin: 0; padding: 0; box-sizing: border-box; }
  html, body {
    width: 1200px; height: 960px; overflow: hidden;
    background: var(--stage);
  }
  .canvas { position: relative; width: 1200px; height: 960px; }

  .card {
    position: absolute;
    left: 320px;
    width: 600px; height: 342px;
    background: var(--navy);
    overflow: hidden;
  }

  /* Front */
  .card-front { top: 108px; }
  .brand {
    position: absolute; left: 0; right: 0; top: 96px;
    display: flex; flex-direction: column; align-items: center;
  }
  .brand-square {
    width: 26px; height: 26px; background: var(--white);
    margin-bottom: 30px;
  }
  .brand-name {
    font-family: "Open Sans", sans-serif; font-weight: 700;
    font-size: 50px; line-height: 1; letter-spacing: -0.5px;
    color: var(--cyan);
  }
  .website {
    position: absolute; left: 0; right: 0; top: 284px;
    text-align: center;
    font-family: "Roboto", sans-serif; font-size: 14px;
    letter-spacing: 6.5px; color: var(--text-light);
  }

  /* Back */
  .card-back { top: 493px; }
  .back-shape { position: absolute; inset: 0; }
  .contact {
    position: absolute; left: 35px; top: 24px;
    font-family: "Roboto", sans-serif; color: var(--text-light);
  }
  .person-name {
    font-family: "Roboto Condensed", sans-serif; font-weight: 500;
    font-size: 21px; color: var(--cyan); text-transform: uppercase;
    letter-spacing: -0.2px;
  }
  .person-title { font-size: 14px; font-weight: 500; margin: 2px 0 0 1px; color: var(--white); }
  .address { margin-top: 56px; font-size: 14.5px; line-height: 19px; }
  .phones { margin-top: 9px; list-style: none; font-size: 14.5px; line-height: 19px; }
  .phones li { display: flex; align-items: center; gap: 8px; }
  .phones svg { width: 15px; height: 14px; fill: var(--cyan); flex: none; }
  .voip { margin-top: 9px; font-size: 14.5px; }

  .back-brand {
    position: absolute; left: 330px; top: 146px; width: 250px;
    display: flex; flex-direction: column; align-items: center;
  }
  .back-brand .brand-square { background: var(--cyan); width: 22px; height: 22px; margin-bottom: 12px; }
  .back-brand .brand-name { font-size: 26px; }
</style>
</head>
<body>
<main class="canvas">

  <section class="card card-front" aria-label="Business card front">
    <div class="brand">
      <span class="brand-square"></span>
      <span class="brand-name">ORIN VANTAGE</span>
    </div>
    <p class="website">www.orinvantage.com</p>
  </section>

  <section class="card card-back" aria-label="Business card back">
    <svg class="back-shape" viewBox="0 0 600 342" aria-hidden="true">
      <polygon points="422,0 600,0 600,342 425,342 252,172" fill="var(--white)"/>
    </svg>

    <div class="contact">
      <h1 class="person-name">Clara Jo Tsang</h1>
      <p class="person-title">VP</p>
      <p class="address">
        APAC M&amp;A Operations<br>
        Orin Vantage Asia Pacific Limited<br>
        Unit 1407, K18<br>
        18 Tai Lok Shan Road<br>
        Hong Kong
      </p>
      <ul class="phones">
        <li>
          <svg viewBox="0 0 16 16" aria-label="Telephone"><path d="M3.6 1l2.3 2.6-1.3 2c.9 2 2.4 3.6 4.6 4.7l2-1.3L14 11.6l-1.6 2.6C7 14 2 9 1.5 3z"/></svg>
          +852 2836 4100
        </li>
        <li>
          <svg viewBox="0 0 16 16" aria-label="Mobile"><path d="M4.5 0.5h7v15h-7zM6 2.5v9.5h4V2.5zM7.3 13h1.4v1.3H7.3z" fill-rule="evenodd"/></svg>
          +852 6038 1742
        </li>
        <li>
          <svg viewBox="0 0 16 16" aria-label="Fax"><path d="M4 1h8v4H4zM1 6h14v6h-2v3H3v-3H1zM5 10v3h6v-3z" fill-rule="evenodd"/></svg>
          +852 2836 4177
        </li>
      </ul>
      <p class="voip">VOIP: 4158</p>
    </div>

    <div class="back-brand">
      <span class="brand-square"></span>
      <span class="brand-name">ORIN VANTAGE</span>
    </div>
  </section>

</main>
</body>
</html>
```